Harborline Family Counsel Billboard

We are looking for a billboard design for a Florida divorce law firm. We are unique in the legal field for offering flat fee pricing. Other law firms are expensive, charging hourly rates. We have A LOT of lawyers advertising for personal injury, so we are looking for something fun that will catch the attention and drive home the message that we are an affordable firm to hire for their divorce because we charge a fixed fee. We want people to be directed to steadyratesplit.com

Target Market(s)

Individual seeking a fast and affordable divorce at a fixed fee instead of hourly

Industry/Entity Type

Legal

Requirements
Must have
• Name of firm, logo, steadyratesplit.com, and in small font: Main Office Coralmont
Should not have
• Promises. Price

```html
<!DOCTYPE html>
<html lang="en">
<head>
<meta charset="UTF-8">
<title>Harborline Family Counsel Billboard</title>
<link href="https://fonts.googleapis.com/css2?family=Anton&family=Cinzel:wght@500&family=Poppins:wght@400;600&display=swap" rel="stylesheet">
<style>
  :root {
    --page: #ffffff;
    --board: #ecebe7;
    --ink: #3b3b3b;
    --navy: #1c3e63;
    --gold: #ad841c;
    --teal-dark: #12303f;
    --teal: #1d4556;
    --amber: #e4a63d;
    --amber-dark: #c98f2e;
    --wall: #8f8a8b;
    --white: #ffffff;
  }
  * { margin: 0; padding: 0; box-sizing: border-box; }
  html, body {
    width: 1199px; height: 1200px; overflow: hidden;
    background: var(--page);
  }
  .canvas { position: relative; width: 1199px; height: 1200px; }
  .billboard {
    position: absolute; left: 50px; top: 440px;
    width: 1100px; height: 320px;
    background: var(--board);
    box-shadow: 0 10px 22px rgba(0,0,0,0.22);
    overflow: hidden;
  }
  .photo-left {
    position: absolute; left: 0; top: 0; width: 187px; height: 100%;
    background: linear-gradient(90deg, var(--teal-dark) 0%, var(--teal) 55%, #8c9398 75%, #5a6e7c 100%);
  }
  .photo-right {
    position: absolute; right: 0; top: 0; width: 182px; height: 100%;
    background: linear-gradient(90deg, #ddd9d6 0%, var(--wall) 14%, #b9b3b2 26%, var(--amber) 30%, #4c5b34 45%, #4c5b34 72%, var(--amber) 80%, var(--amber-dark) 100%);
  }
  .brand {
    position: absolute; left: 356px; top: 24px; height: 70px;
    display: flex; align-items: center; gap: 18px;
  }
  .brand-dot {
    width: 70px; height: 70px; border-radius: 50%;
    background: var(--navy); flex: none;
  }
  .brand-name {
    font-family: "Cinzel", serif; font-weight: 500;
    color: var(--navy); font-size: 24px; line-height: 1.05;
    letter-spacing: 0.5px; white-space: nowrap;
  }
  .headline {
    font-family: "Anton", sans-serif; text-transform: uppercase;
    color: var(--ink); font-weight: 400;
  }
  .headline-line {
    position: absolute; left: 261px; line-height: 1; white-space: nowrap;
  }
  .line-one { top: 112px; font-size: 62px; letter-spacing: 2.6px; }
  .line-two { top: 170px; font-size: 78px; letter-spacing: 6px; }
  .accent-navy { color: var(--navy); }
  .accent-gold { color: var(--gold); }
  .office {
    position: absolute; left: 261px; top: 268px;
    font-family: "Poppins", sans-serif; font-size: 15px; color: var(--ink);
    white-space: nowrap;
  }
  .office strong { font-weight: 600; }
  .url-pill {
    position: absolute; left: 484px; top: 260px;
    width: 354px; height: 34px; border-radius: 17px;
    background: var(--navy); color: var(--white);
    font-family: "Poppins", sans-serif; font-weight: 600;
    font-size: 21px; letter-spacing: 2.6px;
    display: flex; align-items: center; justify-content: center;
  }
</style>
</head>
<body>
<div class="canvas">
  <div class="billboard">
    <div class="photo-left" role="img" aria-label="Photo of a man in a grey t-shirt leaning on a wall with arms crossed, against a dark teal background"></div>
    <div class="photo-right" role="img" aria-label="Photo of a woman in a green sweater leaning in a doorway with arms crossed, against a golden yellow wall"></div>

    <div class="brand">
      <div class="brand-dot"></div>
      <div class="brand-name">Harborline<br>Family Counsel</div>
    </div>

    <h1 class="headline">
      <span class="headline-line line-one">We charge a <span class="accent-navy">fixed fee</span></span>
      <span class="headline-line line-two">On your <span class="accent-gold">divorce</span></span>
    </h1>

    <p class="office">Main Office <strong>Coralmont</strong></p>
    <div class="url-pill">steadyratesplit.com</div>
  </div>
</div>
</body>
</html>
```